New Coffee Shop business card

We are opening our new coffee shop and are needing business cards to take with us on February 6th to Atlanta, Ga to a show.

We will be offering the following menu type items:

coffee
teas
espresso
frappes
smoothies

sandwiches
soups
salads
pastries
ice cream

Our shop is in a rural country-side area and we would like to convey that feel in our shop. In addition to the cafe we will also be selling gifts and furniture and other home decor. Much of this merchandise will be rescued, refurbished or repurposed which is also a core value of what we are all about.

We have a company logo we would like incorporated into the design.

We will also provide files that have the elements of the logo which may also be useful in the design of the card.

Since we are not open yet we need one slightly altered version of the card as well as the final product which states "Opening in the summer 2015"

Target Market(s)

moderate to slightly upscale and folksy.

Industry/Entity Type

Coffee Shop

Contact Information for Business Card

Fern Kettle Coffee
name
address
phone number
email

Card

Font styles to use
Sans Serif

Requirements
Must have
• Must include Logo
• Must include information on menu.
• Must include information on our merchandise sales as described inthe project description.
• Color scheme to complement the logo
Nice to have
• The following descriptions
• "We are also selling gifts, furniture, and other home decoration."
• "We rescue, refurbish, and repurpose old furniture so it can live again."

```html
<!DOCTYPE html>
<html lang="en">
<head>
<meta charset="utf-8">
<title>Fern Kettle Coffee – Business Cards</title>
<link rel="stylesheet" href="https://fonts.googleapis.com/css2?family=Open+Sans:wght@400;600;700&display=swap">
<style>
  :root{
    --stage:#e6e4e2;
    --charcoal:#2b2c2f;
    --paper:#ffffff;
    --wine:#7a2c32;
    --ink:#2a2a2a;
    --muted:#5a5a5a;
    --mist:#efeceb;
    --white:#ffffff;
  }
  *{margin:0;padding:0;box-sizing:border-box}
  html,body{width:1200px;height:768px;overflow:hidden}
  body{
    background:var(--stage);
    font-family:"Open Sans",Arial,sans-serif;
    display:flex;align-items:center;justify-content:center;gap:40px;
  }
  .card{
    position:relative;width:540px;height:310px;overflow:hidden;
    box-shadow:0 6px 18px rgba(0,0,0,.18);
  }
  /* front */
  .card--front{background:var(--charcoal);display:flex;align-items:center;justify-content:center}
  .brand{display:flex;align-items:center;gap:10px;font-weight:400;line-height:1.05}
  .brand__dot{width:14px;height:14px;border-radius:50%;flex:none}
  .card--front .brand{color:var(--white);font-size:30px}
  .card--front .brand__dot{background:var(--white)}
  /* back */
  .card--back{background:var(--paper)}
  .ornament{
    position:absolute;left:290px;top:60px;width:160px;height:150px;
    background:radial-gradient(ellipse at center,var(--mist) 0%,rgba(239,236,235,0) 70%);
  }
  .card--back .brand{position:absolute;left:44px;top:62px;color:var(--ink);font-size:30px}
  .card--back .brand__dot{background:var(--wine)}
  .menu{
    position:absolute;right:26px;top:34px;text-align:right;
    font-size:14px;line-height:1.45;color:var(--ink);list-style:none;
  }
  .merch{
    position:absolute;right:26px;top:146px;width:250px;text-align:right;
    font-size:10.5px;line-height:1.4;color:var(--muted);
  }
  .contact-band{
    position:absolute;left:0;bottom:0;width:320px;height:112px;
    background:var(--wine);color:var(--white);
    padding:18px 0 0 22px;font-size:12.5px;list-style:none;
  }
  .contact-band li{display:flex;align-items:center;gap:7px;margin-bottom:6px}
  .contact-band svg{width:12px;height:12px;flex:none;fill:var(--white)}
  .contact-band .sep{margin-left:10px}
  .person{position:absolute;right:26px;top:196px;text-align:right;color:var(--ink)}
  .person__name{font-weight:700;font-size:17px;line-height:1.3}
  .person__role{font-size:12.5px}
  .web-band{
    position:absolute;right:0;bottom:0;width:220px;height:56px;
    background:var(--charcoal);color:var(--white);
    display:flex;align-items:center;justify-content:center;font-size:13px;
  }
</style>
</head>
<body>
  <section class="card card--front" aria-label="Card front">
    <div class="brand"><span class="brand__dot"></span><span>Fern Kettle<br>Coffee</span></div>
  </section>

  <section class="card card--back" aria-label="Card back">
    <div class="ornament" role="img" aria-label="Faint floral flourish decoration"></div>
    <div class="brand"><span class="brand__dot"></span><span>Fern Kettle<br>Coffee</span></div>

    <ul class="menu">
      <li>Coffee « Teas «</li>
      <li>Soups « Salads «</li>
      <li>Espresso « Frappes «</li>
      <li>Pastries « Ice Cream «</li>
      <li>Smoothies « Sandwiches «</li>
    </ul>

    <p class="merch">Also selling gifts, furniture &amp; home decor.<br>We rescue, refurbish &amp; repurpose old furniture.</p>

    <ul class="contact-band">
      <li>
        <svg viewBox="0 0 12 12" aria-hidden="true"><path d="M2 1h2.5l1 3-1.5 1a6 6 0 0 0 3 3l1-1.5 3 1V10a1 1 0 0 1-1 1A9 9 0 0 1 1 2a1 1 0 0 1 1-1z"/></svg>
        <span>000 0 0 000 00</span>
        <svg class="sep" viewBox="0 0 12 12" aria-hidden="true"><path d="M3 1h6v3H3zM1 5h10v5H1zM3 8h6v3H3z"/></svg>
        <span>(03) 5550 1284</span>
      </li>
      <li>
        <svg viewBox="0 0 12 12" aria-hidden="true"><path d="M1 3h10v7H1zM1 3l5 4 5-4" stroke="#7a2c32" stroke-width="1"/></svg>
        <span>hello@fernkettlecoffee.com</span>
      </li>
      <li>
        <svg viewBox="0 0 12 12" aria-hidden="true"><path d="M6 0a4 4 0 0 1 4 4c0 3-4 8-4 8S2 7 2 4a4 4 0 0 1 4-4zm0 2.5a1.5 1.5 0 1 0 0 3 1.5 1.5 0 0 0 0-3z"/></svg>
        <span>Your long commercial of office address</span>
      </li>
    </ul>

    <div class="person">
      <div class="person__name">Your Long Name</div>
      <div class="person__role">Managing Director</div>
    </div>

    <div class="web-band">www.fernkettlecoffee.com</div>
  </section>
</body>
</html>
```